Newsletter template

I am looking for 2 newsletter templates. My website is in Wordpress and I want to use in mailchimp for lists.

One newsletter is for local clients of design remodeling firm to be sent monthly

Second newsletter is for web store offerings to be sent weekly.

Target Market(s)

Luxury home and leisure

Industry/Entity Type

Store

Requirements
Must have
• Use logos and colors to seamlessly integrate with website,

```html
<!DOCTYPE html>
<html lang="en">
<head>
<meta charset="utf-8">
<title>Maren Vale Newsletter</title>
<link rel="stylesheet" href="https://fonts.googleapis.com/css2?family=Arimo:wght@400;700&family=Open+Sans:wght@400&display=swap">
<style>
  :root {
    --page: #ffffff;
    --tab: #3f3f3f;
    --tab-dash: #6a6a6a;
    --teal: #1a9fc9;
    --teal-button: #22b5cc;
    --teal-button-dark: #1892a5;
    --rule-blue: #4aa3cf;
    --body-text: #777777;
    --placeholder: #464646;
    --tag-yellow: #dcdc00;
    --grey-button: #a9a9a9;
    --grey-button-dark: #8c8c8c;
    --divider: #d8d8d8;
    --social: #9fc9d6;
  }
  html, body {
    margin: 0;
    padding: 0;
    width: 871px;
    height: 1200px;
    overflow: hidden;
    background: var(--page);
  }
  .newsletter {
    position: relative;
    width: 871px;
    height: 1200px;
    overflow: hidden;
    font-family: "Arimo", Arial, sans-serif;
  }
  .newsletter > * { position: absolute; margin: 0; }

  .tab {
    left: 39px; top: 0; width: 255px; height: 72px;
    background: linear-gradient(#474747, #363636);
    box-shadow: 0 3px 6px rgba(0,0,0,.25);
    color: #fff;
    font-family: "Open Sans", Arial, sans-serif;
    font-size: 23px;
    line-height: 72px;
    text-align: center;
  }
  .tab::before {
    content: "";
    position: absolute;
    left: 6px; right: 6px; top: 10px;
    border-top: 1px dashed var(--tab-dash);
  }

  .utility-links {
    right: 13px; top: 3px;
    font-size: 14px;
    color: var(--teal);
  }

  .social { left: 664px; top: 33px; }

  .brand {
    left: 0; width: 894px; top: 82px;
    text-align: center;
    font-size: 50px;
    color: var(--teal);
    letter-spacing: 1px;
  }

  .divider {
    left: 39px; width: 819px; height: 8px;
    background: radial-gradient(ellipse at center, rgba(0,0,0,.16) 0%, rgba(0,0,0,.05) 55%, rgba(0,0,0,0) 75%);
  }
  .divider-top { top: 204px; }
  .divider-mid { top: 798px; }

  .image-slot { background: var(--placeholder); }
  .hero-image { left: 39px; top: 243px; width: 819px; height: 338px; }
  .feature-image { left: 462px; top: 844px; width: 397px; height: 223px; }
  .flexible-image { left: 462px; top: 1126px; width: 397px; height: 90px; }

  .accent-rule {
    left: 39px; top: 607px; width: 819px; height: 5px;
    background: var(--rule-blue);
  }

  .headline {
    font-weight: 400;
    font-size: 23px;
    color: var(--teal);
    line-height: 28px;
  }
  .lead-headline { left: 39px; top: 637px; }
  .feature-headline { left: 39px; top: 892px; }
  .flexible-headline { left: 39px; top: 1174px; }

  .copy {
    font-size: 15px;
    line-height: 26px;
    color: var(--body-text);
  }
  .lead-copy { left: 39px; top: 686px; width: 650px; }
  .feature-copy { left: 39px; top: 932px; width: 400px; }

  .button {
    color: #fff;
    font-weight: 700;
    font-size: 13px;
    letter-spacing: .5px;
    text-align: center;
    line-height: 27px;
    height: 30px;
    box-sizing: border-box;
  }
  .button-view-more {
    left: 730px; top: 640px; width: 129px;
    background: var(--teal-button);
    border-bottom: 3px solid var(--teal-button-dark);
  }
  .button-more {
    left: 39px; top: 1040px; width: 85px;
    background: var(--grey-button);
    border-bottom: 3px solid var(--grey-button-dark);
  }

  .tag {
    height: 30px;
    padding: 0 9px;
    background: var(--tag-yellow);
    color: #fff;
    font-weight: 700;
    font-size: 13.5px;
    line-height: 30px;
  }
  .tag-special { left: 39px; top: 844px; }
  .tag-flexible { left: 39px; top: 1126px; }

  .thin-rule {
    left: 130px; top: 1098px; width: 660px; height: 1px;
    background: linear-gradient(90deg, rgba(216,216,216,0), var(--divider) 30%, var(--divider) 70%, rgba(216,216,216,0));
  }
</style>
</head>
<body>
<main class="newsletter">
  <div class="tab">newsletter</div>

  <p class="utility-links">browser version • text version • unsubscribe</p>

  <svg class="social" width="180" height="38" viewBox="0 0 180 38" aria-label="Social links">
    <circle cx="19" cy="18" r="16" fill="var(--social)"/>
    <circle cx="63" cy="18" r="16" fill="var(--social)"/>
    <circle cx="110" cy="18" r="16" fill="var(--social)"/>
    <circle cx="155" cy="18" r="16" fill="var(--social)"/>
  </svg>

  <p class="brand">Maren Vale</p>

  <div class="divider divider-top"></div>

  <div class="image-slot hero-image" role="img" aria-label="Wide feature photo of a luxury home interior"></div>

  <div class="accent-rule"></div>

  <h2 class="headline lead-headline">Non semper lorem sollicitudin</h2>
  <div class="button button-view-more">VIEW MORE</div>
  <p class="copy lead-copy">Donec porttitor quam vel purus venenatis rutrum. Nullam quam nibh, congue sed aliquet posuere, aliquam non lacus. Maecenas nec luctus neque. Aliquam sagittis tincidunt lectus, non semper lorem sollicitudin ac. Proin ac felis tortor, eu ultricies orci.</p>

  <div class="divider divider-mid"></div>

  <span class="tag tag-special">THE SPECIAL ONE ARTICLE</span>
  <h3 class="headline feature-headline">Quisque convallis</h3>
  <p class="copy feature-copy">Donec porttitor quam vel purus venenatis rutrum. Nullam quam nibh, congue sed aliquet posuere, aliquam non lacus. Maecenas nec luctus neque...</p>
  <div class="button button-more">MORE</div>
  <div class="image-slot feature-image" role="img" aria-label="Article photo of a furnished living space"></div>

  <div class="thin-rule"></div>

  <span class="tag tag-flexible">FLEXIBLE</span>
  <h3 class="headline flexible-headline">Sed eu laoreet metus</h3>
  <div class="image-slot flexible-image" role="img" aria-label="Article photo of home decor"></div>
</main>
</body>
</html>
```